Eye Catching Email Marketing design

Our health care consulting firm is based in New York City. We sell health care consulting Services to medical practices (doctors). We need a powerful email marketing design to use as one of our primary selling tools to attract new clients. The Design should convey health care knowledge, expertise professionalism, cutting edge technology and the services we offer. <br/>The design should incorporate our logo and its colors (blue and white) but we want it to be eye catching and vibrant, so other colors be included. We are open to the designer's creativity. Any pictures used should show diversity (races)and should include women. Designers can find our logo and other graphics on our website at www harbor ridge advisory.com. Please feel free to ask questions.<br/><br/>

Target Market(s)

Health care professionals, executives and Doctors.

Colors

Designer to choose colors to be used in the design.

Requirements
Nice to have
• What ever the design feels will help make this design vibrant

```html
<!DOCTYPE html>
<html lang="en">
<head>
<meta charset="utf-8">
<title>Harbor Ridge Advisory – Advanced Healthcare Operations</title>
<link href="https://fonts.googleapis.com/css2?family=Montserrat:wght@300;400;700;800&family=Open+Sans:wght@400&family=Roboto:wght@400;500&display=swap" rel="stylesheet">
<style>
  :root {
    --navy: #0b3c93;
    --royal: #0d4fa3;
    --sky: #2a8fd0;
    --ink: #3b3b3b;
    --muted: #555;
    --paper: #ffffff;
    --logo-bg: #f3f3f1;
    --footer-bg: #f6f6f6;
    --rule: #d6d6d6;
  }
  * { margin: 0; padding: 0; box-sizing: border-box; }
  html, body { width: 1200px; height: 3801px; overflow: hidden; background: var(--paper); }
  body { position: relative; font-family: "Open Sans", sans-serif; color: var(--ink); }

  .brand-bar { position: absolute; top: 0; left: 0; width: 1200px; height: 195px; background: var(--logo-bg);
    display: flex; align-items: center; justify-content: center; gap: 18px; }
  .brand-mark { width: 26px; height: 26px; border-radius: 50%; background: var(--royal); }
  .brand-name { font-family: "Montserrat", sans-serif; font-weight: 700; font-size: 40px; color: var(--navy); letter-spacing: 1px; }

  .hero-photo { position: absolute; top: 195px; left: 0; width: 1200px; height: 682px;
    background: linear-gradient(180deg, #eef0f2 0%, #dfe4ea 45%, #5a78c0 80%, #2f4f9e 100%); }

  .intro { position: absolute; top: 877px; left: 0; width: 1200px; height: 555px; text-align: center; }
  .intro-kicker { position: absolute; top: 100px; width: 100%; font-family: "Montserrat", sans-serif; font-weight: 800; font-size: 63px; color: var(--sky); letter-spacing: 1px; }
  .intro-title { position: absolute; top: 176px; width: 100%; font-family: "Montserrat", sans-serif; font-weight: 800; font-size: 78px; color: var(--navy); letter-spacing: 1px; }
  .intro-text { position: absolute; top: 282px; left: 100px; width: 1000px; font-size: 30px; line-height: 45px; color: var(--ink); }

  .services { position: absolute; top: 1432px; left: 0; width: 1200px; height: 915px;
    background: linear-gradient(180deg, #0c4ea6 0%, #0a4a9e 60%, #0b4597 100%); color: var(--paper); }
  .services-title { position: absolute; top: 70px; width: 100%; text-align: center; font-family: "Montserrat", sans-serif; font-size: 54px; font-weight: 300; }
  .services-title strong { font-weight: 800; }
  .services-map { position: absolute; top: 0; left: 0; }
  .service-label { position: absolute; font-family: "Montserrat", sans-serif; font-weight: 700; font-size: 30px; line-height: 38px; }
  .service-label.left { text-align: right; }
  .service-hub { position: absolute; top: 438px; width: 100%; text-align: center; font-family: "Montserrat", sans-serif; font-weight: 800; font-size: 100px; letter-spacing: 4px; }

  .tech { position: absolute; top: 2347px; left: 0; width: 1200px; height: 686px; }
  .tech-copy { position: absolute; top: 0; left: 0; width: 603px; height: 686px; background: var(--sky); color: #eef6fc; padding: 110px 0 0 98px; }
  .tech-heading { font-family: "Montserrat", sans-serif; font-size: 42px; line-height: 57px; font-weight: 400; color: var(--paper); }
  .tech-heading strong { display: block; font-weight: 800; }
  .tech-text { margin-top: 30px; width: 450px; font-size: 27px; line-height: 45px; }
  .tech-photo { position: absolute; top: 0; left: 603px; width: 597px; height: 686px;
    background: linear-gradient(160deg, #e9ebee 0%, #cfd4da 45%, #5c5f66 75%, #9c2b55 100%); }

  .contact { position: absolute; top: 3033px; left: 0; width: 1200px; height: 642px; }
  .contact-title { position: absolute; top: 140px; width: 100%; text-align: center; font-family: "Montserrat", sans-serif; font-weight: 800; font-size: 57px; color: var(--navy); }
  .contact-text { position: absolute; top: 220px; left: 100px; width: 1000px; text-align: center; font-size: 30px; line-height: 45px; color: var(--muted); }
  .contact-item { position: absolute; top: 366px; display: flex; align-items: center; gap: 20px; font-family: "Roboto", sans-serif; }
  .contact-item.phone { left: 90px; }
  .contact-item.email { left: 570px; }
  .contact-icon { width: 124px; height: 124px; border-radius: 50%; display: flex; align-items: center; justify-content: center; }
  .phone .contact-icon { background: var(--sky); }
  .email .contact-icon { background: var(--navy); }
  .contact-label { font-size: 28px; color: #111; }
  .contact-value { margin-top: 8px; font-size: 33px; font-weight: 500; color: #111; }

  .footer { position: absolute; top: 3675px; left: 0; width: 1200px; height: 126px; background: var(--footer-bg); border-top: 2px solid var(--rule);
    text-align: center; padding-top: 40px; font-size: 30px; color: var(--muted); }
</style>
</head>
<body>
  <header class="brand-bar">
    <span class="brand-mark"></span>
    <span class="brand-name">Harbor Ridge Advisory LLC</span>
  </header>

  <div class="hero-photo" role="img" aria-label="Photo of four medical professionals in white coats and scrubs reviewing a clipboard together"></div>

  <section class="intro">
    <h2 class="intro-kicker">ADVANCED HEALTHCARE</h2>
    <h1 class="intro-title">OPERATIONS</h1>
    <p class="intro-text">Harbor Ridge Advisory (HRA), founded in 2015, is a Management Services Organization &amp; Healthcare Consulting Firm skilled at helping medical practices advance their strategic vision</p>
  </section>

  <section class="services">
    <h2 class="services-title">OUR <strong>SERVICES</strong></h2>
    <svg class="services-map" width="1200" height="915" viewBox="0 0 1200 915" fill="none" stroke="#fff" stroke-linecap="round" stroke-linejoin="round">
      <!-- connectors -->
      <g stroke="#a9c3e8" stroke-width="2.5">
        <polyline points="372,312 508,312 508,425"/>
        <polyline points="832,312 695,312 695,425"/>
        <polyline points="372,698 508,698 508,585"/>
        <polyline points="832,698 695,698 695,585"/>
      </g>
      <g fill="#a9c3e8" stroke="none">
        <circle cx="372" cy="312" r="8"/><circle cx="832" cy="312" r="8"/>
        <circle cx="372" cy="698" r="8"/><circle cx="832" cy="698" r="8"/>
      </g>
      <!-- revenue cycle icon -->
      <g stroke-width="9">
        <path d="M260 220 A38 38 0 0 1 318 205"/>
        <path d="M334 230 A38 38 0 0 1 310 282"/>
        <path d="M280 286 A38 38 0 0 1 256 240"/>
      </g>
      <g fill="#fff" stroke="none">
        <polygon points="318,192 330,212 306,214"/>
        <polygon points="300,292 312,272 322,294"/>
        <polygon points="246,236 268,236 256,256"/>
      </g>
      <!-- compliance icon -->
      <g stroke-width="8">
        <path d="M870 160 h50 v70 h22 v12 h-62 a14 14 0 0 1 -14 -14 v-56"/>
        <path d="M870 160 a12 12 0 0 0 -12 12 v8 h12"/>
      </g>
      <path d="M906 178 l22 8 v14 c0 14 -10 22 -22 26 c-12 -4 -22 -12 -22 -26 v-14 z" fill="#fff" stroke="none"/>
      <polyline points="896,202 904,210 918,194" stroke="#0c4ea6" stroke-width="5"/>
      <!-- innovation icon -->
      <circle cx="296" cy="560" r="40" stroke-width="9" stroke-dasharray="14 8"/>
      <circle cx="296" cy="548" r="11" fill="#fff" stroke="none"/>
      <path d="M274 586 a22 20 0 0 1 44 0 z" fill="#fff" stroke="none"/>
      <path d="M262 600 h46 l28 -16" stroke-width="9"/>
      <!-- practice management icon -->
      <circle cx="918" cy="516" r="12" stroke-width="7" stroke-dasharray="7 4"/>
      <path d="M876 530 v36 l22 24 v12" stroke-width="8"/>
      <path d="M960 530 v36 l-22 24 v12" stroke-width="8"/>
      <path d="M890 548 l18 22" stroke-width="7"/>
      <path d="M946 548 l-18 22" stroke-width="7"/>
    </svg>
    <div class="service-label left" style="left:60px;top:300px;width:282px;">REVENUE CYCLE<br>MANAGEMENT</div>
    <div class="service-label" style="left:869px;top:300px;">COMPLIANCE<br>MANAGEMENT</div>
    <div class="service-label left" style="left:60px;top:670px;width:282px;">HEALTHCARE<br>INNOVATION</div>
    <div class="service-label" style="left:873px;top:670px;">PRACTICE<br>MANAGEMENT</div>
    <div class="service-hub">HRA</div>
  </section>

  <section class="tech">
    <div class="tech-copy">
      <h2 class="tech-heading">HEALTHCARE<strong>TECHNOLOGY</strong></h2>
      <p class="tech-text">Harbor Ridge Advisory (HRA), founded in 2015, is a Management Services Organization &amp; Healthcare Consulting Firm skilled at helping medical practices advance their strategic vision in an ever-evolving healthcare system.</p>
    </div>
    <div class="tech-photo" role="img" aria-label="Photo of a diverse team of doctors and consultants meeting around a table in a bright office"></div>
  </section>

  <section class="contact">
    <h2 class="contact-title">CONTACT US</h2>
    <p class="contact-text">Harbor Ridge Advisory (HRA), founded in 2015, is a Management Services Organization &amp; Healthcare Consulting Firm skilled</p>
    <div class="contact-item phone">
      <div class="contact-icon">
        <svg width="60" height="60" viewBox="0 0 24 24" fill="#fff"><path d="M6.6 10.8c1.4 2.8 3.8 5.1 6.6 6.6l2.2-2.2c.3-.3.7-.4 1-.2 1.1.4 2.3.6 3.6.6.6 0 1 .4 1 1V20c0 .6-.4 1-1 1C10.6 21 3 13.4 3 4c0-.6.4-1 1-1h3.5c.6 0 1 .4 1 1 0 1.3.2 2.5.6 3.6.1.3 0 .7-.2 1z"/></svg>
      </div>
      <div>
        <div class="contact-label">Phone Number</div>
        <div class="contact-value">(646) 555-0142</div>
      </div>
    </div>
    <div class="contact-item email">
      <div class="contact-icon">
        <svg width="60" height="44" viewBox="0 0 30 22"><rect width="30" height="22" rx="2" fill="#fff"/><polyline points="1,2 15,12 29,2" fill="none" stroke="#0b3c93" stroke-width="2.5"/></svg>
      </div>
      <div>
        <div class="contact-label">Email address</div>
        <div class="contact-value">info@harborridgeadvisory.com</div>
      </div>
    </div>
  </section>

  <footer class="footer">© 2020 Company Name | All Rights Reserved</footer>
</body>
</html>
```